Wealth Education Business Needs Sharp Business Card Design

We need a business card design for a recently launched investor education business called Harbor Crest.

The final design should promote security, empowerment, self improvement and financial gain. The card will ideally promote the stature of the business.

For more information and colours please visit harborcrest.com.au

Target Market(s)

Corporate executives and high net worth individuals

Industry/Entity Type

Education

Contact Information for Business Card

```html
<!DOCTYPE html>
<html lang="en">
<head>
<meta charset="utf-8">
<title>Harbor Crest – Business Card</title>
<link rel="stylesheet" href="https://fonts.googleapis.com/css2?family=Josefin+Sans:wght@400&family=Lato:wght@400;700&family=Cinzel:wght@400;700&display=swap">
<style>
  :root {
    --bg: #e8e8e8;
    --card-white: #ffffff;
    --ink: #3a3a3a;
    --ink-dark: #1e1e1e;
    --green: #5e9e38;
    --green-card-light: #79b24c;
    --green-card-dark: #5f9a34;
    --blue: #2f8fcd;
    --white: #ffffff;
  }
  * { margin: 0; padding: 0; box-sizing: border-box; }
  html, body { width: 1200px; height: 720px; overflow: hidden; }
  body { background: var(--bg); position: relative; font-family: "Lato", sans-serif; }

  .card {
    position: absolute;
    top: 240px;
    width: 420px;
    height: 240px;
    border-radius: 14px;
    overflow: hidden;
  }
  .card-front { left: 148px; background: var(--card-white); }
  .card-back {
    left: 633px;
    background: linear-gradient(135deg, var(--green-card-light), var(--green-card-dark));
  }

  .brand-name {
    position: absolute;
    left: 22px;
    top: 28px;
    font-family: "Josefin Sans", sans-serif;
    font-weight: 400;
    font-size: 29px;
    letter-spacing: 5px;
    color: var(--ink);
    white-space: nowrap;
  }

  .person { position: absolute; left: 20px; top: 86px; }
  .person-name { font-weight: 700; font-size: 16px; color: var(--green); line-height: 1.2; }
  .person-title { font-weight: 700; font-size: 12px; color: var(--ink-dark); margin-top: 2px; }

  .contacts { position: absolute; left: 21px; top: 135px; list-style: none; }
  .contacts li {
    display: flex; align-items: center; gap: 5px;
    font-size: 12.5px; color: var(--ink-dark); line-height: 14.6px;
  }
  .contacts svg { width: 11px; height: 11px; fill: var(--green); flex: none; }

  .address-band {
    position: absolute; left: 0; bottom: 0;
    width: 100%; height: 40px;
    background: var(--blue);
    display: flex; align-items: center; gap: 5px;
    padding-left: 21px;
    color: var(--white); font-size: 12.5px;
  }
  .address-band svg { width: 11px; height: 11px; fill: var(--white); }

  .back-lockup {
    position: absolute; left: 0; top: 0; width: 100%; height: 100%;
    display: flex; flex-direction: column; align-items: center; justify-content: center;
    color: var(--white);
  }
  .back-name {
    font-family: "Josefin Sans", sans-serif;
    font-weight: 400; font-size: 38px; letter-spacing: 4px;
    line-height: 1; padding-top: 10px;
  }
  .back-tagline {
    font-family: "Cinzel", serif;
    font-weight: 700;
    font-size: 15.5px; letter-spacing: 2.8px; margin-top: 2px;
    white-space: nowrap;
  }
</style>
</head>
<body>

<section class="card card-front" aria-label="Business card front">
  <div class="brand-name">HARBOR CREST</div>

  <div class="person">
    <div class="person-name">Liam Carter</div>
    <div class="person-title">Director</div>
  </div>

  <ul class="contacts">
    <li>
      <svg viewBox="0 0 16 16" aria-hidden="true"><path d="M1 5c0-2 3-3 7-3s7 1 7 3v1h-4V5H5v1H1zM4 7h8l2 6H2z"/></svg>
      1300 555 014
    </li>
    <li>
      <svg viewBox="0 0 16 16" aria-hidden="true"><path d="M4 0h8v16H4zM5.5 2v10h5V2z"/></svg>
      +613 9555 0172
    </li>
    <li>
      <svg viewBox="0 0 16 16" aria-hidden="true"><path d="M0 3h16v10H0zM1.5 4.5 8 9l6.5-4.5z"/></svg>
      support@harborcrest.com.au
    </li>
    <li>
      <svg viewBox="0 0 16 16" aria-hidden="true"><path d="M8 0a8 8 0 1 0 0 16A8 8 0 0 0 8 0zm0 1.5c.9 0 2 1.9 2.3 5H5.7C6 3.4 7.1 1.5 8 1.5zM1.6 6.5h2.6c.1-1.8.5-3.3 1.1-4.4a6.5 6.5 0 0 0-3.7 4.4zm9-4.4c.6 1.1 1 2.6 1.2 4.4h2.6a6.5 6.5 0 0 0-3.8-4.4zM1.6 9.5a6.5 6.5 0 0 0 3.7 4.4c-.6-1.1-1-2.6-1.1-4.4zm4.1 0c.3 3.1 1.4 5 2.3 5s2-1.9 2.3-5zm6.1 0c-.2 1.8-.6 3.3-1.2 4.4a6.5 6.5 0 0 0 3.8-4.4z"/></svg>
      www.harborcrest.com.au
    </li>
  </ul>

  <div class="address-band">
    <svg viewBox="0 0 16 16" aria-hidden="true"><path d="M8 1 0 8h2v7h4.5v-4h3v4H14V8h2z"/></svg>
    Level 2, 48 Harbour Street, Melbourne VIC 3000
  </div>
</section>

<section class="card card-back" aria-label="Business card back">
  <div class="back-lockup">
    <div class="back-name">HARBOR CREST</div>
    <div class="back-tagline">STUDY BUILD FLOURISH</div>
  </div>
</section>

</body>
</html>
```